Business Card and Letterhead for Pimlu - modern real estate business

I need a double sided business card design for Pimlu. Please see business card brief here https://files.trelvonadocs.com/sheet/r/7QzTmWbaXLJnoPEd-kRyUgFhHsstbvCe2qfoMxDa_pz/view?mode=shared

Please feel free to design the business cards however you feel best. I am happy to give some creative freedoms and then provide feedback from there.

Please then also create a letterhead to match the business card design

Colors

Designer to choose colors to be used in the design.

Requirements
Must have
• Must be a modern, elegant business card which looks very professional

```html
<!DOCTYPE html>
<html lang="en">
<head>
<meta charset="UTF-8">
<title>Pimlu – Business Card and Letterhead</title>
<link rel="stylesheet" href="https://fonts.googleapis.com/css2?family=Exo+2:wght@400;500;600&display=swap">
<style>
  :root {
    --red: #e3222a;
    --charcoal: #1c1c1c;
    --white: #ffffff;
    --backdrop: #e9e9e9;
    --faint-red: #fbeeee;
    --rule-grey: #6a6a6a;
  }
  * { margin: 0; padding: 0; box-sizing: border-box; }
  html, body { width: 1200px; height: 1200px; overflow: hidden; }
  body {
    position: relative;
    background: var(--backdrop);
    font-family: "Exo 2", sans-serif;
    color: var(--white);
  }
  .wordmark {
    font-family: "Exo 2", sans-serif;
    font-weight: 600;
    color: var(--red);
    letter-spacing: 0.04em;
    line-height: 1;
    white-space: nowrap;
  }

  /* Letterhead */
  .letterhead {
    position: absolute; left: 268px; top: 170px;
    width: 667px; height: 863px;
    background: var(--white);
    overflow: hidden;
    box-shadow: 4px 6px 14px rgba(0,0,0,0.18);
  }
  .letterhead .wordmark {
    position: absolute; top: 50px; left: 0; width: 100%;
    text-align: center; font-size: 60px;
  }
  .letterhead-backmark {
    position: absolute; left: 26px; top: 676px;
    font-family: "Exo 2", sans-serif; font-weight: 600;
    font-size: 190px; line-height: 1; letter-spacing: 0.04em;
    color: var(--faint-red); white-space: nowrap;
  }
  .letterhead-footer {
    position: absolute; left: 0; bottom: 0; width: 100%; height: 71px;
    background: var(--charcoal);
    border-top: 2px solid var(--red);
    text-align: center;
  }
  .footer-address { margin-top: 12px; font-size: 12.5px; letter-spacing: 0.04em; }
  .footer-rule { width: 308px; height: 1px; background: var(--rule-grey); margin: 6px auto 0; }
  .footer-contacts {
    display: flex; justify-content: center; gap: 10px;
    margin-top: 7px; font-size: 12.5px; letter-spacing: 0.05em;
  }
  .contact-item { display: flex; align-items: center; gap: 4px; }
  .icon { width: 10px; height: 10px; flex: none; }

  /* Business card front */
  .card-front {
    position: absolute; left: 92px; top: 358px;
    width: 350px; height: 200px;
    background: var(--white);
    overflow: hidden;
    box-shadow: 4px 6px 14px rgba(0,0,0,0.22);
  }
  .card-front-band {
    position: absolute; left: 0; top: 99px; width: 100%; height: 101px;
    background: var(--charcoal);
    border-top: 1.5px solid var(--red);
  }
  .card-front .wordmark {
    position: absolute; left: 215px; top: 24px; font-size: 23px;
  }
  .agent-photo {
    position: absolute; left: 67px; top: 55px; width: 82px; height: 90px;
    background: var(--white); border: 1.5px solid var(--red); padding: 2.5px;
  }
  .agent-photo-fill {
    width: 100%; height: 100%;
    background: linear-gradient(180deg, #9fb5a8 0%, #7d8a5e 45%, #2b2b2d 70%, #1d1d20 100%);
  }
  .agent-name {
    position: absolute; left: 0; top: 153px; width: 216px; text-align: center;
    font-size: 14px; font-weight: 500; color: var(--red); letter-spacing: 0.05em;
  }
  .agent-title {
    position: absolute; left: 0; top: 168px; width: 216px; text-align: center;
    font-size: 8px; letter-spacing: 0.06em;
  }
  .card-contacts {
    position: absolute; left: 215px; top: 115px;
    font-size: 8px; line-height: 10.4px; letter-spacing: 0.05em;
  }
  .card-contacts .contact-item { gap: 6px; }
  .card-contacts .icon { width: 7px; height: 7px; }

  /* Business card back */
  .card-back {
    position: absolute; left: 781px; top: 358px;
    width: 350px; height: 200px;
    background: var(--charcoal);
    border: 1.5px solid var(--red);
    box-shadow: 4px 6px 14px rgba(0,0,0,0.22);
    display: flex; align-items: center; justify-content: center;
  }
  .card-back .wordmark { font-size: 60px; }
</style>
</head>
<body>

<svg width="0" height="0" style="position:absolute" aria-hidden="true">
  <defs>
    <symbol id="icon-phone" viewBox="0 0 24 24">
      <path fill="#e3222a" d="M6.6 10.8c1.4 2.8 3.8 5.1 6.6 6.6l2.2-2.2c.3-.3.7-.4 1-.2 1.1.4 2.3.6 3.6.6.6 0 1 .4 1 1V20c0 .6-.4 1-1 1C10.6 21 3 13.4 3 4c0-.6.4-1 1-1h3.5c.6 0 1 .4 1 1 0 1.3.2 2.5.6 3.6.1.3 0 .7-.2 1l-2.3 2.2z"/>
    </symbol>
    <symbol id="icon-mail" viewBox="0 0 24 24">
      <rect x="2.5" y="5" width="19" height="14" rx="1.5" fill="none" stroke="#e3222a" stroke-width="2"/>
      <path d="M3 6l9 7 9-7" fill="none" stroke="#e3222a" stroke-width="2"/>
    </symbol>
    <symbol id="icon-globe" viewBox="0 0 24 24">
      <g fill="none" stroke="#e3222a" stroke-width="1.8">
        <circle cx="12" cy="12" r="9.5"/>
        <ellipse cx="12" cy="12" rx="4.2" ry="9.5"/>
        <path d="M2.5 12h19M4 7h16M4 17h16"/>
      </g>
    </symbol>
  </defs>
</svg>

<section class="letterhead">
  <div class="wordmark">PIMLU</div>
  <div class="letterhead-backmark" aria-hidden="true">PIMLU</div>
  <footer class="letterhead-footer">
    <p class="footer-address">PO Box 5172, Larkhaven NSW 2790</p>
    <div class="footer-rule"></div>
    <div class="footer-contacts">
      <span class="contact-item"><svg class="icon"><use href="#icon-phone"/></svg>0412 583 904</span>
      <span class="contact-item"><svg class="icon"><use href="#icon-phone"/></svg>1300 640 218</span>
      <span class="contact-item"><svg class="icon"><use href="#icon-mail"/></svg>Reid@pimlu.com</span>
      <span class="contact-item"><svg class="icon"><use href="#icon-globe"/></svg>www.pimlu.com</span>
    </div>
  </footer>
</section>

<section class="card-front">
  <div class="card-front-band"></div>
  <div class="wordmark">PIMLU</div>
  <div class="agent-photo">
    <div class="agent-photo-fill" role="img" aria-label="Portrait photo of the agent in a dark suit, outdoors"></div>
  </div>
  <p class="agent-name">REID CALDER</p>
  <p class="agent-title">Licenced Real Estate Agent</p>
  <div class="card-contacts">
    <p>PO Box 5172</p>
    <p>Larkhaven NSW 2790</p>
    <p class="contact-item"><svg class="icon"><use href="#icon-phone"/></svg>0412 583 904</p>
    <p class="contact-item"><svg class="icon"><use href="#icon-phone"/></svg>1300 640 218</p>
    <p class="contact-item"><svg class="icon"><use href="#icon-mail"/></svg>Reid@pimlu.com</p>
    <p class="contact-item"><svg class="icon"><use href="#icon-globe"/></svg>www.pimlu.com</p>
  </div>
</section>

<section class="card-back">
  <div class="wordmark">PIMLU</div>
</section>

</body>
</html>
```